Creative Card Game Card Design for a Unique Universe

We are designing a physical card game whose closest cousin is "Sorcery: The Assembling" (http://www.quillforge.example/Runes). We are in need of a CREATIVE design for the cards that is similar, but different and unique, compared to other card games. Card designs should fit within the fantasy realm, but ultimately be portable to other genres, such as science fiction or medieval.

The fundamentals of our cards include:
• Title (up to ~3 long-ish words)
• Card type icon (attack, defend, augmented attack, augmented defend)
• Image (majority of the card)
• Instructional text area 1 (up to ~25 words)
• Instructional text area 2 (up to ~30 words)
• Copyright area
• Game logo area

The back of the card identifies each type of card with a different background with the game logo and title in front of it (probably white). Current ideas for backgrounds identifying the different types of cards are fiery red, metallic silver, marble green, and brown leather, so feel free to suggest textures for those as well.

Areas where we are looking for creativity:
• Textures and backgrounds (e.g. we like the parchment/antique paper look)
• Interesting use of transparency and/or gradient colors
• Shape and positioning of elements (but still needs to be functional)
• Overlapping of elements
• Card borders (if they make sense in your design)
• Icon style
• Fonts (we use "Lindsay EF" in our manual)
• Card size (but still needs to be usable in the player's hand; standard size is ~2.5" x 3.5")
• Card shape (but still needs to be usable in the player's hand; e.g. Rectangular but with a rounded corner)

Restrictions on the design:
• Design should be in color
• Card shape can be creative (but not too "out there"), but should be a reasonable cost to print
• First priority is to print, but cards will also be used in an iPad app

Tools:
• We would prefer the design was submitted in Adobe Illustrator format (vector-based)

We will give extra attention to designs that are truly unique and that we haven't seen before!

For examples of Runes cards, see http://www.quillforge.example/runes/tcg/article.aspx?x=rtb/tcg/runes2013/pod

Thank you!
Updates

Hi there,

Appreciate you thinking about our little card design project! Just wanted to provide an update that I uploaded another file (a logo) on request, and also updated the comments with some sample text for a card, also on request.

Thanks,

Oliver.

Reason: Our small team isn't meeting until Wed to discuss the designs, so extending until we've had a chance to discuss the designs. Thanks, Oliver.

Target Market(s)

Teenagers+, English-speaking to start

Industry/Entity Type

Games

Font styles to use
Other font styles liked:
• Lindsay EF

Colors

Designer to choose colors to be used in the design.

Requirements
Should not have
• An identical look to other card games, like Runes.

```html
<!DOCTYPE html>
<html lang="en">
<head>
<meta charset="utf-8">
<title>Swing – Card</title>
<link rel="stylesheet" href="https://fonts.googleapis.com/css2?family=Uncial+Antiqua&family=Almendra:wght@400;700&display=swap">
<style>
  :root {
    --ink: #0b0a08;
    --parchment: #d8c98a;
    --parchment-light: #efe4b0;
    --parchment-dark: #a8954e;
    --oval-top: #6e6a48;
    --oval-mid: #57532f;
    --oval-bottom: #4a4627;
    --oval-rim: #d9cf9c;
    --text-cream: #e6e1c4;
    --title-cream: #ddd8b6;
    --disc-ink: #4b4228;
    --badge-fill: #5a4428;
    --badge-ring: #8a6a3a;
  }
  html, body {
    margin: 0;
    padding: 0;
    width: 777px;
    height: 1200px;
    overflow: hidden;
    background: var(--ink);
  }
  .card {
    position: relative;
    width: 777px;
    height: 1200px;
    background: var(--ink);
  }
  .card-frame {
    position: absolute;
    inset: 0;
  }
  .card-text {
    position: absolute;
    left: 0;
    top: 0;
    width: 777px;
    height: 1200px;
  }
  .card-title {
    position: absolute;
    top: 634px;
    left: 0;
    width: 777px;
    margin: 0;
    text-align: center;
    font-family: "Uncial Antiqua", fantasy;
    font-size: 52px;
    line-height: 70px;
    font-weight: 400;
    letter-spacing: 1px;
    color: var(--title-cream);
    text-shadow: 2px 3px 3px rgba(0,0,0,0.75);
  }
  .card-rules {
    position: absolute;
    top: 720px;
    left: 146px;
    width: 540px;
    margin: 0;
    font-family: "Almendra", serif;
    font-size: 30px;
    line-height: 41px;
    white-space: nowrap;
    color: var(--text-cream);
    text-shadow: 1px 2px 2px rgba(0,0,0,0.7);
  }
  .card-rules p { margin: 0; }
  .card-rules .effect { margin-top: 41px; }
  .card-copyright {
    position: absolute;
    top: 1092px;
    left: 0;
    width: 777px;
    margin: 0;
    text-align: center;
    font-family: "Almendra", serif;
    font-size: 17px;
    line-height: 26px;
    color: var(--text-cream);
    opacity: 0.85;
  }
  .corner-value {
    position: absolute;
    font-family: "Uncial Antiqua", fantasy;
    color: var(--disc-ink);
    text-align: center;
  }
  .corner-type {
    left: 630px;
    top: 50px;
    width: 114px;
    font-size: 54px;
    line-height: 86px;
  }
  .corner-cost {
    left: 46px;
    top: 1050px;
    width: 124px;
    font-size: 50px;
    line-height: 86px;
  }
</style>
</head>
<body>
<div class="card">
  <svg class="card-frame" width="777" height="1200" viewBox="0 0 777 1200" xmlns="http://www.w3.org/2000/svg">
    <defs>
      <linearGradient id="parchment-fill" x1="0" y1="0" x2="1" y2="1">
        <stop offset="0" stop-color="var(--parchment-light)"/>
        <stop offset="0.5" stop-color="var(--parchment)"/>
        <stop offset="1" stop-color="var(--parchment-dark)"/>
      </linearGradient>
      <linearGradient id="oval-fill" x1="0" y1="0" x2="0" y2="1">
        <stop offset="0" stop-color="var(--oval-top)"/>
        <stop offset="0.45" stop-color="var(--oval-mid)"/>
        <stop offset="1" stop-color="var(--oval-bottom)"/>
      </linearGradient>
      <radialGradient id="disc-fill" cx="0.45" cy="0.4" r="0.6">
        <stop offset="0" stop-color="#f7f2dd"/>
        <stop offset="1" stop-color="#d9cfa8"/>
      </radialGradient>
    </defs>

    <rect class="border-parchment" x="26" y="26" width="725" height="1148" fill="url(#parchment-fill)" stroke="#2a2414" stroke-width="3"/>

    <g class="art-oval">
      <ellipse cx="388" cy="606" rx="346" ry="572" fill="url(#oval-fill)"/>
      <ellipse class="art-illustration" role="img" aria-label="Pencil sketch of a helmeted warrior swinging a large weapon, in muted olive tones"
               cx="388" cy="330" rx="300" ry="290" fill="#7d7857" opacity="0.45"/>
      <ellipse cx="388" cy="606" rx="346" ry="572" fill="none" stroke="var(--oval-rim)" stroke-width="4"/>
      <ellipse cx="388" cy="606" rx="338" ry="564" fill="none" stroke="#3a3520" stroke-width="2" opacity="0.7"/>
    </g>

    <circle class="type-badge type-badge-top" cx="103" cy="103" r="66" fill="var(--badge-fill)" stroke="var(--badge-ring)" stroke-width="4"/>
    <circle class="type-badge type-badge-bottom" cx="672" cy="1102" r="66" fill="var(--badge-fill)" stroke="var(--badge-ring)" stroke-width="4"/>

    <circle class="disc disc-type" cx="687" cy="93" r="58" fill="url(#disc-fill)" stroke="#8a7a48" stroke-width="4"/>
    <circle class="disc disc-cost" cx="108" cy="1093" r="62" fill="url(#disc-fill)" stroke="#8a7a48" stroke-width="4"/>
  </svg>

  <div class="card-text">
    <div class="corner-value corner-type">S</div>
    <div class="corner-value corner-cost">10</div>

    <h1 class="card-title">SWING</h1>

    <div class="card-rules">
      <p>Requirement: None</p>
      <p>Optional Cost: Any attack card or any<br>2 cards for +1 damage; or additional<br>SWING card for +2</p>
      <p class="effect">Effect: SWING damage</p>
    </div>

    <p class="card-copyright">©Copyright 2014<br>All Rights Reserved.</p>
  </div>
</div>
</body>
</html>
```